Business Card: RW Office Partners - Your organised problem solver

Business Name: RW Office Partners
Website: www.rwofficepartners.com.au
Email: marisol@rwofficepartners.com.au
Mobile: 61 482 907 236
Facebook: @rwofficepartners
Instrgram: @rwofficepartners

Brading Colours:
HEX
#986474
#ddccd3
#7a8498
#c9d8e4
#000000
#ffffff

Tag Line: Your organised problem solver

Link to DRAFT website:
https://deskhelpcollective.wixsite.com/rw-office-partners

About Page from the website:
My name is Marisol Wrenfield, and I would love to assist you to become more productive in your day to day and achieve your business and personal goals.
My mission is to give you time, time to work on the important tasks of your business or to be able to spend more time with your family. I will take on the tasks you don’t have time for, don’t know well or simply don’t like to do.
I have an extensive background in Administration, Tender Coordination, Document Control, WHS and Quality Management working primarily in the Construction, Mining and Corporate World.
I am passionate about being organised, having order and making things in your life (and mine) easier! I love to watch something unfold and grow into something amazing! I am known for being the go-to problem solver, the organiser of all things, producing high standards of work even under pressure. I’m also a confident communicator, and I understand that you’re busy running your business.

Target Market(s)

Small to Medium Business who require assistance in their business by a virtual assistant.

Industry/Entity Type

Virtual Assistant

Contact Information for Business Card

Mobile: 61 482 907 236

Font styles to use
Sans Serif

Colors
ffffff

Requirements
Must have
• Branding Colours as outlined.
Contact Details as outlined.
Logo as provided.
Proper contact details - mobile, facebook, instragm, website.
Simple, Elegant, very clean looking.
Should not have
• Note cute with pictures.
Not too girly as still want to market to construction companies.

```html
<!DOCTYPE html>
<html lang="en">
<head>
<meta charset="utf-8">
<title>RW Office Partners – Business Card</title>
<link href="https://fonts.googleapis.com/css2?family=Montserrat:wght@500&family=Roboto:wght@400;700&family=Roboto+Mono:wght@400&display=swap" rel="stylesheet">
<style>
  :root {
    --mauve: #986474;
    --mauve-light: #ddccd3;
    --slate: #7a8498;
    --ice: #c9d8e4;
    --ink: #000000;
    --card-black: #1c1b1e;
    --white: #ffffff;
    --stage: #3b3b3d;
    --logo-grey: #5d5d62;
  }
  * { box-sizing: border-box; margin: 0; padding: 0; }
  html, body {
    width: 799px; height: 1200px; overflow: hidden;
    background: var(--stage);
  }
  .canvas {
    position: relative; width: 799px; height: 1200px;
  }
  .card {
    position: absolute; left: 70px; width: 660px; height: 377px;
    background: var(--card-black); overflow: hidden;
    box-shadow: 0 12px 30px rgba(0,0,0,.45);
  }
  .card--front { top: 150px; }
  .card--back { top: 680px; }

  /* Front */
  .front-brand {
    position: absolute; left: 0; right: 0; top: 130px; text-align: center;
    font-family: "Montserrat", sans-serif; font-weight: 500;
    font-size: 52px; letter-spacing: 1px; color: var(--logo-grey);
  }
  .front-social {
    position: absolute; left: 0; right: 0; top: 262px;
    display: flex; justify-content: center; gap: 34px;
    font-family: "Roboto", sans-serif; font-size: 17px; color: var(--white);
  }
  .social-item { display: flex; align-items: center; gap: 9px; }
  .social-dot {
    width: 13px; height: 13px; border-radius: 2px; background: var(--mauve);
  }

  /* Back */
  .back-brand {
    position: absolute; left: 40px; top: 42px;
    font-family: "Montserrat", sans-serif; font-weight: 500;
    font-size: 40px; color: var(--mauve);
  }
  .back-tagline {
    position: absolute; left: 42px; top: 96px;
    font-family: "Roboto Mono", monospace; font-size: 15px;
    letter-spacing: 3px; color: var(--white);
  }
  .person-name {
    position: absolute; left: 42px; top: 138px;
    font-family: "Roboto", sans-serif; font-weight: 700;
    font-size: 21px; color: var(--mauve);
  }
  .person-role {
    position: absolute; left: 42px; top: 166px;
    font-family: "Roboto", sans-serif; font-size: 14px; color: var(--white);
  }
  .wave { position: absolute; inset: 0; width: 660px; height: 377px; }
  .contact-list {
    position: absolute; right: 28px; top: 248px; list-style: none;
    font-family: "Roboto", sans-serif; font-size: 16px; color: var(--white);
  }
  .contact-list li {
    display: flex; justify-content: flex-end; align-items: center;
    gap: 12px; height: 23px;
  }
  .contact-icon { width: 15px; height: 15px; flex: none; }
  .contact-square {
    width: 13px; height: 13px; border-radius: 2px; background: var(--white); flex: none; margin: 0 1px;
  }
</style>
</head>
<body>
<main class="canvas">

  <section class="card card--front" aria-label="Card front">
    <div class="front-brand">RW Office Partners</div>
    <div class="front-social">
      <span class="social-item"><span class="social-dot"></span>@rwofficepartners</span>
      <span class="social-item"><span class="social-dot"></span>@rwofficepartners</span>
    </div>
  </section>

  <section class="card card--back" aria-label="Card back">
    <svg class="wave" viewBox="0 0 660 377" aria-hidden="true">
      <path d="M0 212 C160 185 310 275 660 218 L660 230 C310 288 160 200 0 226 Z" fill="var(--slate)"/>
      <path d="M0 232 C160 206 310 296 660 238 L660 377 L0 377 Z" fill="var(--mauve)"/>
    </svg>

    <div class="back-brand">RW Office Partners</div>
    <div class="back-tagline">Your organised problem solver</div>
    <div class="person-name">Marisol Wrenfield</div>
    <div class="person-role">Virtual Assistant</div>

    <ul class="contact-list">
      <li>61 482 907 236
        <svg class="contact-icon" viewBox="0 0 16 16" aria-hidden="true"><path d="M3 1h3l1.5 4-2 1.2a9 9 0 0 0 4.3 4.3L11 8.5l4 1.5v3a2 2 0 0 1-2 2A12 12 0 0 1 1 3a2 2 0 0 1 2-2z" fill="var(--white)"/></svg>
      </li>
      <li>marisol@rwofficepartners.com.au
        <svg class="contact-icon" viewBox="0 0 16 16" aria-hidden="true"><rect x="1" y="3" width="14" height="10" fill="var(--white)"/><path d="M1 3l7 6 7-6" fill="none" stroke="var(--mauve)" stroke-width="1.4"/></svg>
      </li>
      <li>www.rwofficepartners.com.au
        <svg class="contact-icon" viewBox="0 0 16 16" aria-hidden="true"><g fill="none" stroke="var(--white)" stroke-width="1.4"><circle cx="8" cy="8" r="6.5"/><ellipse cx="8" cy="8" rx="3" ry="6.5"/><path d="M1.5 8h13"/></g></svg>
      </li>
      <li>@rwofficepartners <span class="contact-square"></span></li>
      <li>@rwofficepartners <span class="contact-square"></span></li>
    </ul>
  </section>

</main>
</body>
</html>
```